Coastline Premier Retreats Business Card Design

Design a business card for Coastline Premier Retreats. Look at the website for colors and reference. Card should have logo, name, title, office number, mobile number, email, URL and a tagline like, "Luxury Hotel & Resort Email Marketing" (This might change).

https://www.coastlinepremierretreats.example

The rest I will leave up to your imagination.

Contact Information for Business Card

Logo, name, title, office number, mobile number, email, URL and a tagline like, "Luxury Hotel & Resort Email Marketing" (This might change).

```html
<!DOCTYPE html>
<html lang="en">
<head>
<meta charset="utf-8">
<title>Coastline Premier Retreats — Business Card</title>
<link rel="stylesheet" href="https://fonts.googleapis.com/css2?family=Open+Sans:wght@400;600;700&display=swap">
<style>
  :root {
    --stage: #222222;
    --brand-orange: #f37521;
    --paper: #fefdf6;
    --ink: #111111;
    --white: #ffffff;
  }
  * { box-sizing: border-box; margin: 0; padding: 0; }
  html, body {
    width: 1200px; height: 780px; overflow: hidden;
    background: var(--stage);
    font-family: "Open Sans", Arial, sans-serif;
  }
  .canvas { position: relative; width: 1200px; height: 780px; }

  .card {
    position: absolute; width: 525px; height: 300px;
    overflow: hidden;
    box-shadow: 0 18px 40px rgba(0,0,0,.45);
  }

  /* Back: contact side */
  .card-back { left: 45px; top: 240px; background: var(--paper); }
  .tagline-band {
    position: absolute; left: 0; top: 0; width: 62px; height: 100%;
    background: var(--brand-orange);
  }
  .tagline {
    position: absolute; left: 31px; top: 150px;
    transform: translate(-50%, -50%) rotate(-90deg);
    width: 280px; text-align: center;
    color: var(--white); font-size: 12.5px; line-height: 1.3; letter-spacing: .3px;
  }
  .wordmark {
    position: absolute; right: 34px; top: 30px;
    display: flex; align-items: center; gap: 9px;
  }
  .wordmark-square { width: 14px; height: 14px; background: var(--brand-orange); }
  .wordmark-name {
    font-weight: 700; font-size: 17px; text-transform: uppercase;
    letter-spacing: 1px; color: var(--ink);
  }
  .contact-block {
    position: absolute; right: 34px; top: 108px; text-align: right;
  }
  .person-name { font-weight: 700; font-size: 26px; color: var(--ink); line-height: 1.1; }
  .person-name .given { color: var(--brand-orange); }
  .person-title { font-size: 13.5px; color: var(--ink); margin-top: 2px; }
  .contact-list { list-style: none; margin-top: 14px; }
  .contact-list li {
    display: flex; justify-content: flex-end; align-items: center; gap: 8px;
    font-size: 12.5px; color: var(--ink); line-height: 1.55;
  }
  .contact-list svg { width: 12px; height: 12px; fill: var(--brand-orange); flex: none; }
  .edge-tab {
    position: absolute; right: 0; top: 192px; width: 12px; height: 44px;
    background: var(--brand-orange);
  }

  /* Front: brand side */
  .card-front { left: 630px; top: 240px; background: var(--brand-orange); }
  .front-wordmark {
    position: absolute; inset: 0;
    display: flex; align-items: center; justify-content: center; gap: 14px;
  }
  .front-wordmark-square { width: 22px; height: 22px; background: var(--white); }
  .front-wordmark-name {
    font-weight: 700; font-size: 25px; text-transform: uppercase;
    letter-spacing: 1.5px; color: var(--white);
  }
</style>
</head>
<body>
<main class="canvas">

  <section class="card card-back" aria-label="Business card, contact side">
    <div class="tagline-band">
      <p class="tagline">Luxury Hotel &amp;<br>Resort Email Marketing</p>
    </div>

    <div class="wordmark">
      <span class="wordmark-square"></span>
      <span class="wordmark-name">Coastline Premier Retreats</span>
    </div>

    <div class="contact-block">
      <h1 class="person-name"><span class="given">Marta</span> Velikova</h1>
      <p class="person-title">Co-Founder</p>
      <ul class="contact-list">
        <li>(555) 014-2758
          <svg viewBox="0 0 24 24" aria-hidden="true"><path d="M6.6 10.8a15.1 15.1 0 0 0 6.6 6.6l2.2-2.2c.3-.3.7-.4 1-.2 1.1.4 2.3.6 3.6.6.6 0 1 .4 1 1V20c0 .6-.4 1-1 1A17 17 0 0 1 3 4c0-.6.4-1 1-1h3.5c.6 0 1 .4 1 1 0 1.3.2 2.5.6 3.6.1.3 0 .7-.2 1z"/></svg>
        </li>
        <li>(555) 019-7777
          <svg viewBox="0 0 24 24" aria-hidden="true"><path d="M7 1h10a2 2 0 0 1 2 2v18a2 2 0 0 1-2 2H7a2 2 0 0 1-2-2V3a2 2 0 0 1 2-2zm0 3v15h10V4zm5 16.2a.9.9 0 1 0 0 1.8.9.9 0 0 0 0-1.8z"/></svg>
        </li>
        <li>www.coastlinepremierretreats.example
          <svg viewBox="0 0 24 24" aria-hidden="true"><path d="M12 2a10 10 0 1 0 0 20 10 10 0 0 0 0-20zm6.9 6h-3a15.7 15.7 0 0 0-1.3-3.9A8 8 0 0 1 18.9 8zM12 4c.8 1.2 1.5 2.5 1.9 4h-3.8c.4-1.5 1.1-2.8 1.9-4zM4.3 14a8.2 8.2 0 0 1 0-4h3.4a16.5 16.5 0 0 0 0 4zm.8 2h3a15.7 15.7 0 0 0 1.3 3.9A8 8 0 0 1 5.1 16zm3-8h-3a8 8 0 0 1 4.3-3.9A15.7 15.7 0 0 0 8.1 8zM12 20c-.8-1.2-1.5-2.5-1.9-4h3.8c-.4 1.5-1.1 2.8-1.9 4zm2.3-6H9.7a14.7 14.7 0 0 1 0-4h4.6a14.7 14.7 0 0 1 0 4zm.3 5.9c.6-1.2 1-2.5 1.3-3.9h3a8 8 0 0 1-4.3 3.9zm1.7-5.9a16.5 16.5 0 0 0 0-4h3.4a8.2 8.2 0 0 1 0 4z"/></svg>
        </li>
        <li>info@coastlinepremierretreats.example
          <svg viewBox="0 0 24 24" aria-hidden="true"><path d="M2 5h20v14H2zm2 2v.5l8 5 8-5V7zm0 2.9V17h16V9.9l-8 5z"/></svg>
        </li>
      </ul>
    </div>

    <span class="edge-tab"></span>
  </section>

  <section class="card card-front" aria-label="Business card, brand side">
    <div class="front-wordmark">
      <span class="front-wordmark-square"></span>
      <span class="front-wordmark-name">Coastline Premier Retreats</span>
    </div>
  </section>

</main>
</body>
</html>
```